TLK Electricial Contracting Services

Hi guys, after a design for my small electrical company, have logo design files to be incorporated into the layout, the basic concept is electrical contracting services for residential, commercial, industrial & data services, image is clean clear and strong,

Card format is to have a nice clean logo on front,with maybe the Residential – commercial – industrial - data, followed with licensed & insured, followed by contact details on backside of the card.

Target Market(s)

Residential, commercial, industrial sectors.

Industry/Entity Type

Electrical

Contact Information for Business Card

TLK logo,
Residential – commercial – industrial - data
REC: 61307
Email: tlk@vornamail.net.au
Phone: 0487 352 019

Requirements
Must have
• Clean & strong design.
Nice to have
• If possible, I would like the logo colours inverted so the text is orange and the background is black on the front of the card, then the backside of the card be the reverse colour
Should not have
• No Sparks, lightning bolts,

```html
<!DOCTYPE html>
<html lang="en">
<head>
<meta charset="UTF-8">
<title>TLK Electrical – Business Cards</title>
<link href="https://fonts.googleapis.com/css2?family=Lato:wght@400;700&display=swap" rel="stylesheet">
<style>
  :root {
    --stage: #2b2724;
    --card: #0c0c0c;
    --orange: #f28c1e;
    --ink: #ffffff;
    --ink-soft: #e6e6e6;
    --divider: #3a3a3a;
  }
  * { box-sizing: border-box; margin: 0; padding: 0; }
  html, body {
    width: 1200px;
    height: 844px;
    overflow: hidden;
    background: var(--stage);
    font-family: "Lato", Arial, sans-serif;
  }
  .stage {
    width: 1200px;
    height: 844px;
    display: flex;
    align-items: center;
    justify-content: center;
    gap: 60px;
  }
  .card {
    width: 520px;
    height: 297px;
    background: var(--card);
    position: relative;
    box-shadow: 0 12px 30px rgba(0,0,0,0.45);
  }
  .wordmark {
    font-weight: 700;
    line-height: 1;
    color: var(--orange);
  }
  .wordmark-initials { letter-spacing: 2px; }
  .wordmark-name { letter-spacing: 0.3px; margin-top: 6px; }

  /* Back side: wordmark + contact details */
  .card-back {
    display: flex;
    align-items: center;
    padding: 0 30px 0 40px;
  }
  .back-brand { width: 200px; }
  .back-brand .wordmark-initials { font-size: 70px; }
  .back-brand .wordmark-name { font-size: 14px; }
  .divider {
    width: 1px;
    height: 190px;
    background: var(--divider);
    margin: 0 26px 0 10px;
  }
  .details { color: var(--ink-soft); font-size: 14px; line-height: 1.35; }
  .person-name { font-size: 20px; color: var(--ink); }
  .person-role { font-size: 13px; margin-bottom: 14px; }
  .licence { margin-bottom: 14px; }
  .label { color: var(--orange); }

  /* Front side: centred wordmark, sectors, licence line */
  .card-front {
    display: flex;
    flex-direction: column;
    align-items: center;
    justify-content: center;
    text-align: center;
  }
  .card-front .wordmark-initials { font-size: 96px; }
  .card-front .wordmark-name { font-size: 17px; }
  .sectors {
    margin-top: 22px;
    font-size: 14px;
    color: var(--ink-soft);
    letter-spacing: 0.4px;
  }
  .insured {
    margin-top: 8px;
    font-size: 12px;
    color: var(--orange);
    letter-spacing: 1.5px;
    text-transform: uppercase;
  }
</style>
</head>
<body>
<main class="stage">
  <section class="card card-back" aria-label="Card back">
    <div class="back-brand">
      <div class="wordmark wordmark-initials">TLK</div>
      <div class="wordmark wordmark-name">TLK Electrical</div>
    </div>
    <div class="divider"></div>
    <div class="details">
      <p class="person-name">Daniel Harper</p>
      <p class="person-role">Managing Director</p>
      <p class="licence">Licensed &amp; Insured<br><span class="label">REC:</span> 61307</p>
      <p><span class="label">P:</span> 0487 352 019</p>
      <p><span class="label">E:</span> tlk@vornamail.net.au</p>
    </div>
  </section>
  <section class="card card-front" aria-label="Card front">
    <div class="wordmark wordmark-initials">TLK</div>
    <div class="wordmark wordmark-name">TLK Electrical</div>
    <p class="sectors">Residential – Commercial – Industrial – Data</p>
    <p class="insured">Licensed &amp; Insured</p>
  </section>
</main>
</body>
</html>
```